Medical Prescription for Diagnostic Sleep Testing

Quiet Harbor Rest Diagnostics main marketing tool is our Prescription that we leave with medical providers. Prescription is printed on 8.5 x 11 sheets of paper to create a prescription pad for our medical providers. Prescription should fit to one page. Quiet Harbor Rest Diagnostics works with 250 different medical providers so it is important we are able to update and change the medical provider information at bottom. The medical provider would fill-out top with patient information, check-off center testing and patient co-morbidity and Fax to Quiet Harbor Rest Diagnostics. Because it is Faxed to us it is important to have clear print and large font Attached or uploaded file is one example we currently use. Please review all 5 must haves.

Target Market(s)

Prescription for medical providers to fill-out and fax to Quiet Harbor Rest Diagnostics to conduct the sleep study.

Industry/Entity Type

Medical

Colors

Designer to choose only greyscale colors for use in the design.

Requirements
Must have
• 1) Prescription Size: 8.5 x 11
• 2) Must fit to One page Only
• 3) Ability to change medical provider information at bottom of prescription. We work with 250 different medical providers
• 4) Ability to change or update any part of prescription
• 5) Document Must be created in Microsoft Word 2016. This is the program we use for our prescriptions.
Nice to have
• Can be done in Gray-Scale or Black and White since its being faxed from the medical provider to us.

```html
<!DOCTYPE html>
<html lang="en">
<head>
<meta charset="utf-8">
<title>Sleep Study Physician Order – Quiet Harbor Rest Diagnostics</title>
<link href="https://fonts.googleapis.com/css2?family=Arimo:ital,wght@0,400;0,700;1,400&display=swap" rel="stylesheet">
<style>
:root{
  --band:#4a4a4a;
  --ink:#1f1f1f;
  --paper:#ffffff;
  --rule:#555555;
  --dots:#8a8a8a;
}
*{box-sizing:border-box;margin:0;padding:0}
html,body{width:929px;height:1200px;overflow:hidden;background:var(--paper)}
body{font-family:"Arimo",Arial,sans-serif;color:var(--ink);position:relative}
.abs{position:absolute}
.header-band{left:23px;top:0;width:877px;height:148px;background:var(--band);color:#fff}
.title-main{left:25px;top:26px;font-weight:700;font-size:43px;line-height:1;letter-spacing:.5px}
.title-sub{left:25px;top:70px;font-weight:700;font-size:31px;line-height:1}
.title-divider{left:347px;top:27px;width:2px;height:78px;background:#fff}
.brand-name{left:361px;top:38px;font-size:29px;line-height:1;font-weight:400}
.brand-sub{left:362px;top:75px;font-size:22px;line-height:1}
.badge{left:589px;top:29px;width:288px;height:73px;background:#fff}
.contact-line{left:25px;top:119px;font-size:13.6px;font-weight:700;white-space:nowrap}
.field{font-size:14.5px;display:flex;align-items:baseline;white-space:nowrap}
.field .line{flex:1;border-bottom:1.5px dotted var(--dots);margin-left:8px;height:12px}
.section-band{left:23px;top:272px;width:877px;height:41px;background:var(--band);color:#fff;font-weight:700;font-size:28px;text-align:center;line-height:41px}
.order{left:23px;width:860px}
.order h3{font-size:16.3px;font-weight:700;display:flex;align-items:center;line-height:1.2}
.order h3::before{content:"";width:9px;height:9px;border-radius:50%;background:var(--ink);margin-right:12px;flex:none}
.order p{font-size:14.4px;margin-left:21px;margin-top:6px;line-height:1.28}
.order p.just{text-align:justify;width:837px}
.necessity{left:23px;top:727px;width:877px;height:190px;border:1px solid var(--rule)}
.necessity-head{background:var(--band);color:#fff;font-weight:700;font-size:15px;text-align:center;height:26px;line-height:26px}
.col{top:36px;font-size:14.4px;line-height:21.3px}
.box{display:inline-block;width:10px;height:10px;border:1px solid var(--ink);margin-right:7px;vertical-align:-1px}
.indent{padding-left:17px}
.other-line{display:inline-block;width:138px;border-bottom:1.5px dotted var(--dots);margin-left:5px}
.provider-band{left:23px;top:933px;width:877px;height:52px;background:var(--band);color:#fff}
.provider-name{left:11px;top:14px;font-size:24px;font-weight:700;white-space:nowrap}
.provider-contact{left:439px;top:8px;font-size:14px;font-weight:700;line-height:17.5px;white-space:nowrap}
.clinician{font-size:14.5px;white-space:nowrap}
.clinician small{font-size:9px}
.footer-band{left:0;top:1094px;width:929px;height:61px;background:var(--band);color:#fff;text-align:center}
.footer-main{font-weight:700;font-size:23px;padding-top:7px;line-height:1.1}
.footer-sub{font-weight:700;font-size:13.4px;margin-top:4px}
.footer-sub .box{border-color:#fff;width:9px;height:9px;margin-right:4px}
.thanks{left:0;width:929px;top:1170px;text-align:center;font-style:italic;font-size:15.5px;letter-spacing:2px}
</style>
</head>
<body>
<header class="abs header-band">
  <div class="abs title-main">SLEEP STUDY</div>
  <div class="abs title-sub">PHYSICIAN ORDER</div>
  <div class="abs title-divider"></div>
  <div class="abs brand-name">QUIET HARBOR</div>
  <div class="abs brand-sub">REST DIAGNOSTICS</div>
  <div class="abs badge" role="img" aria-label="Accreditation badge"></div>
  <div class="abs contact-line">PHONE: (555) 210-4417 &nbsp;•&nbsp; FAX: (555) 210-4418 &nbsp;•&nbsp; ADDRESS: 820 W. Lantern Avenue, Suite 3-C; Springfield, NV 89000</div>
</header>

<div class="abs field" style="left:23px;top:166px;width:364px">Patient Name<span class="line"></span></div>
<div class="abs field" style="left:403px;top:166px;width:170px">DOB<span class="line"></span></div>
<div class="abs field" style="left:600px;top:166px">Patient Gender (circle one)<span style="margin-left:28px">M</span><span style="margin-left:46px">F</span></div>
<div class="abs field" style="left:23px;top:200px;width:303px">Telephone<span class="line"></span></div>
<div class="abs field" style="left:352px;top:200px;width:298px">Primary Insurance<span class="line"></span></div>
<div class="abs field" style="left:672px;top:200px;width:228px">Weight<span class="line"></span></div>
<div class="abs field" style="left:23px;top:234px;width:304px">Alternate Telephone<span class="line"></span></div>
<div class="abs field" style="left:351px;top:234px;width:299px">Secondary Insurance<span class="line"></span></div>
<div class="abs field" style="left:672px;top:234px;width:228px">Height<span class="line"></span></div>

<div class="abs section-band">DIAGNOSTIC SLEEP STUDY ORDERED</div>

<section class="abs order" style="top:415px;top:415px;top:415px;top:415px;top:332px">
  <h3>COMPLETE SLEEP STUDY: (BASED ON INSURANCE OR PATIENT’S CHOICE)</h3>
  <p class="just">In-Lab Sleep Study (PSG) or Home Sleep Study (PSG 95810 / HST 95806) with follow-up PAP Titration Study (PAP 95811 if positive for sleep apnea)</p>
</section>
<section class="abs order" style="top:408px">
  <h3>PEDIATRIC SLEEP STUDY: PSG W/END TIDAL CO2 MONITORING</h3>
  <p>(PSG 95782 under 6 years of age &amp; PSG 95810 older than 6 years of age)</p>
</section>
<section class="abs order" style="top:467px">
  <h3>IN-LAB DIAGNOSTIC SLEEP STUDY / POLYSOMNOGRAM</h3>
  <p>(PSG 95810)</p>
</section>
<section class="abs order" style="top:528px">
  <h3>SPLIT-NIGHT STUDY</h3>
  <p>(PSG with PAP 95810 &amp; 95811) To Comply With Accreditation &amp; Insurance<br><b>Guidelines:</b> AHI must be 20 or greater with minimum 2 hour recorded sleep time &amp; 3 hours minimum to complete PAP treatment.</p>
</section>
<section class="abs order" style="top:605px">
  <h3>CPAP / BIPAP / BIPAP ST TITRATION STUDY</h3>
  <p>(Patients with documented sleep apnea 95811)</p>
</section>
<section class="abs order" style="top:667px">
  <h3>HOME SLEEP STUDY</h3>
  <p>(HST 95806 Conducted in patient’s home and unattended by technologist) (No insurance patient cost $250.00)</p>
</section>

<section class="abs necessity">
  <div class="necessity-head">PATIENT MEDICAL NECESSITY – PLEASE CHECK ALL BOXES THAT APPLY</div>
  <div class="abs col" style="left:11px">
    <div><span class="box"></span>Atrial Fibrillation</div>
    <div><span class="box"></span>Bipolar Disorder</div>
    <div><span class="box"></span>Congestive Heart Failure</div>
    <div><span class="box"></span>COPD</div>
    <div><span class="box"></span>Depression</div>
    <div><span class="box"></span>Excessive Daytime</div>
    <div><span class="box"></span>Sleepiness</div>
  </div>
  <div class="abs col" style="left:231px">
    <div><span class="box"></span>Frequent Urination</div>
    <div><span class="box"></span>Gasping Sensations with</div>
    <div class="indent">Frequent Awakenings</div>
    <div><span class="box"></span>Heart Disease</div>
    <div><span class="box"></span>History Heart Attack</div>
    <div><span class="box"></span>Hypertension</div>
    <div><span class="box"></span>PTSD</div>
  </div>
  <div class="abs col" style="left:449px">
    <div><span class="box"></span>Insomnia</div>
    <div><span class="box"></span>Mental or Mood Disorder</div>
    <div><span class="box"></span>Loud Snoring</div>
    <div><span class="box"></span>Morbid Obesity / Obesity</div>
    <div><span class="box"></span>Morning Headaches</div>
    <div><span class="box"></span>Narcolepsy</div>
    <div><span class="box"></span>Opioid Use</div>
  </div>
  <div class="abs col" style="left:669px">
    <div><span class="box"></span>Pulmonary Disease</div>
    <div><span class="box"></span>Restless Leg Syndrome</div>
    <div><span class="box"></span>Seizures</div>
    <div><span class="box"></span>Shift Work Sleep disorder</div>
    <div><span class="box"></span>Stroke / TIA</div>
    <div><span class="box"></span>Witnessed Apnea</div>
    <div><span class="box"></span>Other<span class="other-line"></span></div>
  </div>
</section>

<section class="abs provider-band">
  <div class="abs provider-name">DESERT VALLEY ENT CLINIC</div>
  <div class="abs provider-contact">PHONE: 555-318-2290 &nbsp;&nbsp;&nbsp;&nbsp;•&nbsp;&nbsp;&nbsp;&nbsp; FAX: 555-318-2291<br>ADDRESS: 4175 N. Mesa Drive, Springfield, NV 89000-1234</div>
</section>

<div class="abs clinician" style="left:23px;top:993px"><span class="box"></span>Dr. Owen Michael Castell <small>( NPI: 1000000001 )</small></div>
<div class="abs clinician" style="left:355px;top:993px"><span class="box"></span>Dr. Reid A. Holloway <small>( NPI: 1000000002 )</small></div>
<div class="abs clinician" style="left:603px;top:993px"><span class="box"></span>Dr. Lena Marsh <small>( NPI: 1000000003 )</small></div>
<div class="abs clinician" style="left:23px;top:1022px"><span class="box"></span>Dr. Victor P. Brandauer <small>( NPI: 1000000004 )</small></div>
<div class="abs clinician" style="left:355px;top:1022px"><span class="box"></span>Neil Harmon, PA-C <small>( NPI: 1000000005 )</small></div>
<div class="abs clinician" style="left:603px;top:1022px"><span class="box"></span>Tessa Norland, FNP-C <small>( NPI: 1000000006 )</small></div>

<div class="abs field" style="left:23px;top:1060px;width:591px">Physician’s Signature<span class="line"></span></div>
<div class="abs field" style="left:630px;top:1060px;width:270px">Date<span class="line"></span></div>

<footer class="abs footer-band">
  <div class="footer-main">Please Fax: 555-210-4418 or Email: rest@quietharbor-example.com</div>
  <div class="footer-sub"><span class="box"></span>Fax Along With: Patient Demographic Information &nbsp;•&nbsp; Copy of Current Insurance Information &nbsp;•&nbsp; Clinical Notes</div>
</footer>

<div class="abs thanks">THANK YOU FOR YOUR SUPPORT MARA AND TED</div>
</body>
</html>
```